Creative Law Firm Business Card

attached are photos of myself and our office as well as language that I would like to see on the card, likely on the back, although I leave that to the designer. I have also attached copies of both sides of a marketing card that we produced just for ideas. I would like to find a tactful way to get my photo in along with the office. I attached copies of our logo, both normal and inverted.

I listed my name as Tom Halloway to be casual, however, it should probably read Thomas J Halloway

Requirements
Must have
• attached file #8 has content.
• I would like my picture and the office photo on page 1
• The text, with the exception of the firm name "HALLOWAY & PEMBER" and the firm description underneath it "THE BUSINESS AND BANKRUPTCY LAWYERS", should be on the back. The layout and fonts are up to the designer

```html
<!DOCTYPE html>
<html lang="en">
<head>
<meta charset="utf-8">
<title>Halloway &amp; Pember — Business Card</title>
<link href="https://fonts.googleapis.com/css2?family=Cinzel:wght@400;500&family=Crimson+Text:wght@400;600&display=swap" rel="stylesheet">
<style>
  :root {
    --bg: #e4e4e4;
    --navy: #1c2a5a;
    --navy-deep: #16224b;
    --sky-blue: #6fa8dc;
    --teal: rgba(0, 128, 150, 0.78);
    --white: #ffffff;
    --ink: #1c2a5a;
    --muted: #3a4468;
    --rule: #c9cdd8;
  }
  * { box-sizing: border-box; margin: 0; padding: 0; }
  html, body { width: 1200px; height: 852px; overflow: hidden; }
  body {
    background: var(--bg);
    position: relative;
    font-family: "Crimson Text", Georgia, serif;
  }
  .card {
    position: absolute;
    width: 530px;
    height: 302px;
    border-radius: 20px;
    overflow: hidden;
    box-shadow: 0 6px 18px rgba(0,0,0,0.18);
  }

  /* ---------- Front ---------- */
  .card-front { left: 40px; top: 275px; }
  .front-scene {
    position: absolute; inset: 0;
    background:
      linear-gradient(160deg, #2f5fd0 0%, #3d77e0 30%, #9fb4c8 55%, #d8cbb3 70%, #8a8577 100%);
  }
  .front-portrait {
    position: absolute;
    left: 40px; bottom: 0;
    width: 230px; height: 240px;
    border-radius: 115px 115px 0 0;
    background: linear-gradient(180deg, #b58f7c 0%, #8b6a5e 40%, #1d1d22 62%, #121216 100%);
  }
  .front-band {
    position: absolute;
    right: 0; top: 112px;
    width: 330px; height: 82px;
    background: var(--teal);
    padding: 10px 18px 0 24px;
    color: var(--white);
    text-align: right;
  }
  .front-firm {
    font-family: "Cinzel", "Times New Roman", serif;
    font-size: 30px;
    letter-spacing: 1px;
    line-height: 1.1;
  }
  .front-tagline {
    font-family: "Crimson Text", Georgia, serif;
    font-size: 14px;
    letter-spacing: 0.6px;
    margin-top: 4px;
  }

  /* ---------- Back ---------- */
  .card-back { left: 630px; top: 275px; background: var(--white); }
  .back-topstrip {
    position: absolute; left: 0; right: 0; top: 0; height: 9px;
    background: var(--sky-blue);
  }
  .back-brand {
    position: absolute; left: 34px; top: 86px; width: 200px;
    text-align: center; color: var(--ink);
  }
  .brand-mark {
    width: 46px; height: 46px; margin: 0 auto 10px;
    background: var(--navy);
  }
  .brand-name {
    font-family: "Cinzel", "Times New Roman", serif;
    font-size: 19px;
    letter-spacing: 0.5px;
    padding-top: 6px;
    border-top: 1px solid var(--navy);
  }
  .back-divider {
    position: absolute; left: 252px; top: 40px; height: 140px;
    border-left: 1px solid var(--rule);
  }
  .back-contact {
    position: absolute; left: 272px; top: 36px; right: 20px;
    color: var(--ink);
  }
  .contact-name {
    font-family: "Cinzel", "Times New Roman", serif;
    font-size: 17px;
    letter-spacing: 0.4px;
  }
  .contact-title {
    font-size: 12.5px; line-height: 1.15; color: var(--muted); margin-top: 2px;
  }
  .contact-address { font-size: 14px; margin-top: 24px; }
  .contact-line {
    display: flex; align-items: center; gap: 8px;
    font-size: 14px; margin-top: 3px;
  }
  .contact-line svg { width: 12px; height: 12px; flex: none; fill: var(--ink); }
  .back-band {
    position: absolute; left: 0; right: 0; bottom: 0; height: 100px;
    background: linear-gradient(180deg, var(--navy) 0%, var(--navy-deep) 100%);
    color: var(--white);
    padding: 12px 14px 0;
    text-align: center;
    font-size: 12.5px;
    line-height: 1.45;
  }
  .band-heading { font-size: 13.5px; letter-spacing: 0.5px; }
  .band-points { text-align: left; }
</style>
</head>
<body>

  <section class="card card-front" aria-label="Card front">
    <div class="front-scene" role="img" aria-label="Photo of the office building under a blue sky with palm trees"></div>
    <div class="front-portrait" role="img" aria-label="Portrait photo of the attorney in a dark suit and tie"></div>
    <div class="front-band">
      <div class="front-firm">HALLOWAY &amp; PEMBER</div>
      <div class="front-tagline">THE BUSINESS &amp; BANKRUPTCY LAWYERS</div>
    </div>
  </section>

  <section class="card card-back" aria-label="Card back">
    <div class="back-topstrip"></div>

    <div class="back-brand">
      <div class="brand-mark"></div>
      <div class="brand-name">HALLOWAY &amp; PEMBER</div>
    </div>

    <div class="back-divider"></div>

    <div class="back-contact">
      <div class="contact-name">Thomas J Halloway</div>
      <div class="contact-title">Bankruptcy Specialist –<br>Court Mediator</div>
      <div class="contact-address">2180 Marlow Ave Cedar Vale CA 90412</div>
      <div class="contact-line">
        <svg viewBox="0 0 24 24" aria-hidden="true"><path d="M6.6 10.8a15.1 15.1 0 0 0 6.6 6.6l2.2-2.2c.3-.3.7-.4 1-.2 1.1.4 2.3.6 3.6.6.6 0 1 .4 1 1V20c0 .6-.4 1-1 1C10.6 21 3 13.4 3 4c0-.6.4-1 1-1h3.5c.6 0 1 .4 1 1 0 1.3.2 2.5.6 3.6.1.3 0 .7-.2 1z"/></svg>
        <span>555-318-4260</span>
      </div>
      <div class="contact-line">
        <svg viewBox="0 0 24 24" aria-hidden="true"><path d="M2 5h20v14H2z M3.5 6.5 12 13l8.5-6.5" fill="none" stroke="currentColor" stroke-width="0"/><path d="M2 5h20v14H2V5zm2 1.8V17h16V6.8l-8 6-8-6z"/></svg>
        <span>tom@hallowaypember.com</span>
      </div>
      <div class="contact-line">
        <svg viewBox="0 0 24 24" aria-hidden="true"><path d="M12 2a10 10 0 1 0 0 20 10 10 0 0 0 0-20zm6.9 6h-3a15.6 15.6 0 0 0-1.4-3.6A8 8 0 0 1 18.9 8zM12 4c.8 1.2 1.5 2.5 1.9 4h-3.8c.4-1.5 1.1-2.8 1.9-4zM4.3 14a8 8 0 0 1 0-4h3.4a16 16 0 0 0 0 4H4.3zm.8 2h3a15.6 15.6 0 0 0 1.4 3.6A8 8 0 0 1 5.1 16zm3-8h-3a8 8 0 0 1 4.4-3.6C8.9 5.6 8.4 6.8 8.1 8zM12 20c-.8-1.2-1.5-2.5-1.9-4h3.8c-.4 1.5-1.1 2.8-1.9 4zm2.3-6H9.7a14 14 0 0 1 0-4h4.6a14 14 0 0 1 0 4zm.2 5.6c.6-1.1 1.1-2.3 1.4-3.6h3a8 8 0 0 1-4.4 3.6zm1.8-5.6a16 16 0 0 0 0-4h3.4a8 8 0 0 1 0 4h-3.4z"/></svg>
        <span>www.hallowaypember.com</span>
      </div>
    </div>

    <div class="back-band">
      <div class="band-heading">36 YEARS EXPERIENCE AV RATED</div>
      <div class="band-points">
        » We find an exit strategy before we act » Practice since 1979 av rated<br>
        » General counsel for your business compressive » Business &amp; litigation services<br>
        » A century of collective experience » Bankruptcy and Reorganizations Collections
      </div>
    </div>
  </section>

</body>
</html>
```